Consulting company business cards

We have a base design, but would be willing to update. We have a new logo/"tag" that needs to be added. Current business card design is attached for reference into our "style."

Industry/Entity Type

Business

Contact Information for Business Card

Should contain name and title, office number, mobile number if appropriate, e-mail, website, physical address, and company logo.

Font styles to use
Other font styles liked:
• See current card design on KorvandBCard

Colors
0455a3
85acd3
aaaaaa

Requirements
Must have
• Our colors are navy blue, gray, and a lighter blue
Nice to have
• Design that I can easily drop in new names/titles as we hire employees.

```html
<!DOCTYPE html>
<html lang="en">
<head>
<meta charset="utf-8">
<title>Brennick Business Cards</title>
<link rel="stylesheet" href="https://fonts.googleapis.com/css2?family=Source+Sans+3:wght@400;600;700&display=swap">
<style>
  :root {
    --navy: #06304f;
    --light-blue: #85acd3;
    --gray: #aaaaaa;
    --white: #ffffff;
    --backdrop: #e9ebee;
  }
  * { margin: 0; padding: 0; box-sizing: border-box; }
  html, body {
    width: 1200px; height: 900px; overflow: hidden;
    background: var(--backdrop);
    font-family: "Source Sans 3", "Myriad Pro", sans-serif;
    color: var(--white);
  }
  .canvas { position: relative; width: 1200px; height: 900px; }
  .card {
    position: absolute;
    overflow: hidden;
    background: var(--navy);
    box-shadow: 0 6px 18px rgba(0,0,0,0.18);
  }
  .card--front { left: 238px; top: 62px; width: 555px; height: 343px; }
  .card--back { left: 457px; top: 518px; width: 560px; height: 343px; }

  .lockup { position: absolute; display: flex; flex-direction: column; }
  .brand { display: flex; align-items: center; }
  .brand__name { font-weight: 700; line-height: 1; letter-spacing: 0.5px; color: var(--white); }
  .brand__mark { flex: none; border-radius: 50%; background: var(--light-blue); }
  .brand__tagline { letter-spacing: 1.5px; color: var(--white); text-transform: uppercase; white-space: nowrap; }

  .card--front .lockup { left: 34px; top: 50px; align-items: flex-start; }
  .card--front .brand { gap: 7px; }
  .card--front .brand__name { font-size: 44px; }
  .card--front .brand__mark { width: 38px; height: 38px; }
  .card--front .brand__tagline { margin-top: 8px; font-size: 11px; }

  .person { position: absolute; left: 33px; top: 161px; }
  .person__name { font-size: 20px; font-weight: 600; line-height: 1.2; }
  .person__title { font-size: 15px; line-height: 1.3; }
  .divider { position: absolute; left: 0; top: 220px; width: 367px; height: 1px; background: var(--gray); }
  .contact { position: absolute; left: 33px; top: 235px; font-size: 15.5px; line-height: 1; }
  .contact__line { height: 23px; white-space: nowrap; }
  .contact__line--address { margin-bottom: 8px; }
  .sep { display: inline-block; margin: 0 14px; }
  .sep--tight { margin: 0 8px; }

  .card--back .lockup { left: 0; right: 0; top: 122px; align-items: center; }
  .card--back .brand { gap: 10px; }
  .card--back .brand__name { font-size: 66px; }
  .card--back .brand__mark { width: 58px; height: 58px; }
  .card--back .brand__tagline { margin-top: 10px; font-size: 15.5px; letter-spacing: 2px; }
  .card--back .site { position: absolute; left: 0; right: 0; top: 275px; text-align: center; font-size: 15.5px; }
</style>
</head>
<body>
<main class="canvas">
  <section class="card card--front">
    <div class="lockup">
      <div class="brand">
        <span class="brand__name">BRENNICK</span>
        <span class="brand__mark"></span>
      </div>
      <p class="brand__tagline">A Cloud Consulting Company</p>
    </div>
    <div class="person">
      <p class="person__name">Dana Korvand</p>
      <p class="person__title">Office Manager</p>
    </div>
    <div class="divider"></div>
    <div class="contact">
      <p class="contact__line contact__line--address">1187 W 54th St Fairview Indiana 46011</p>
      <p class="contact__line">555.014.2910<span class="sep">|</span>555.014.2971</p>
      <p class="contact__line">dkorvand@brennicktech.com<span class="sep sep--tight">|</span>brennicktech.com</p>
    </div>
  </section>

  <section class="card card--back">
    <div class="lockup">
      <div class="brand">
        <span class="brand__name">BRENNICK</span>
        <span class="brand__mark"></span>
      </div>
      <p class="brand__tagline">A Cloud Consulting Company</p>
    </div>
    <p class="site">brennicktech.com</p>
  </section>
</main>
</body>
</html>
```